I need a logo design for a new company based in Tucson called "Mindtrail Lee Corwin". I am a psychotherapist that specializes in clinical psychology with athletes and performers. The final design should incorporate the psychology symbol as a watermark. The logo should convey movement and fluidity. "Mindtrail" is a bit of a play on words combining psychology (head) with sports (coach). Other design interests include mid-century, Harold Ames Whitby. I will want to use the logo for business cards, letterhead and marketing brochures. I will put together a website at a later date. I am attaching a file with some pertinent information for the business card. Thank you.
Lee Corwin
mindtrailleecorwin@quillpost.net

Thank you all for the submissions so far.  I have submitted an additional file with a draft of a new design idea.  Since "mindtrail" is a bit of a play on words, I would like to see something with the two "H's" look something like quotation marks.  If the psychology logo is to be included at all, it needs to be less prominent.     Thank you all.  Lee                               

Target Market(s)

1) Adolescent and adult athletes and performers who are looking to increase their level of performance (Sport and Performance Psychology)
2) Adult psychotherapy patients (Clinical psychology)

Industry/Entity Type

Marketing

Colors

Designer to choose colors to be used in the design.

Requirements
Must have
• 1) Since "mindtrail" is a bit of a play on words, The "H's" need to be in a font that looks somewhat like quotation marks.

Nice to have
• Logo on one side. All other info on the backside?

```html
<!DOCTYPE html>
<html lang="en">
<head>
<meta charset="utf-8">
<title>Mindtrail – Business Card</title>
<link href="https://fonts.googleapis.com/css2?family=Alegreya:wght@700&family=Lato:wght@400;700;900&display=swap" rel="stylesheet">
<style>
  :root {
    --page-bg: #1c1c1d;
    --card-bg: #3e3e40;
    --gold-light: #ecbc2c;
    --gold-dark: #9a7a30;
    --gold-text: #d4a22a;
    --white: #ffffff;
  }
  * { box-sizing: border-box; margin: 0; padding: 0; }
  html, body {
    width: 1200px;
    height: 900px;
    overflow: hidden;
    background: var(--page-bg);
  }
  .canvas {
    position: relative;
    width: 1200px;
    height: 900px;
  }
  .card {
    position: absolute;
    left: 250px;
    width: 700px;
    height: 400px;
    background: var(--card-bg);
    border-radius: 18px;
    overflow: hidden;
  }
  .card--front { top: 40px; }
  .card--back  { top: 460px; }

  /* Front */
  .brand-band {
    position: absolute;
    left: 120px;
    top: 105px;
    width: 460px;
    height: 140px;
    background: linear-gradient(100deg, var(--gold-light) 0%, #c99c2c 55%, var(--gold-dark) 100%);
    display: flex;
    align-items: center;
    justify-content: center;
  }
  .brand-name {
    font-family: 'Lato', sans-serif;
    font-weight: 900;
    font-size: 78px;
    color: var(--white);
    letter-spacing: 1px;
  }
  .brand-tagline {
    position: absolute;
    left: 120px;
    top: 260px;
    width: 460px;
    font-family: 'Lato', sans-serif;
    font-weight: 700;
    font-size: 22px;
    letter-spacing: 2.2px;
    color: var(--white);
    text-align: center;
    white-space: nowrap;
  }

  /* Back */
  .person {
    position: absolute;
    top: 70px;
    width: 100%;
    text-align: center;
  }
  .person-name {
    font-family: 'Alegreya', serif;
    font-weight: 700;
    font-size: 46px;
    color: var(--gold-text);
    letter-spacing: 0.5px;
  }
  .person-title {
    font-family: 'Lato', sans-serif;
    font-weight: 700;
    font-size: 20px;
    color: var(--white);
    margin-top: 2px;
  }
  .contact {
    position: absolute;
    top: 215px;
    width: 100%;
    list-style: none;
    text-align: center;
    font-family: 'Lato', sans-serif;
    font-size: 20px;
    line-height: 34px;
    color: var(--white);
  }
  .contact-label {
    font-weight: 700;
    color: var(--gold-text);
  }
</style>
</head>
<body>
<main class="canvas">
  <section class="card card--front" aria-label="Card front">
    <div class="brand-band">
      <span class="brand-name">Mindtrail</span>
    </div>
    <p class="brand-tagline">CLINICAL &amp; PERFORMANCE PSYCHOLOGY</p>
  </section>

  <section class="card card--back" aria-label="Card back">
    <div class="person">
      <h1 class="person-name">Lee H. Corwin, MA, LLC</h1>
      <p class="person-title">Licensed Professional Counselor</p>
    </div>
    <ul class="contact">
      <li><span class="contact-label">Fax:</span> 520.555.0147</li>
      <li><span class="contact-label">Mobile:</span> 520.555.0182</li>
      <li><span class="contact-label">Email:</span> mindtrailleecorwin@quillpost.net</li>
      <li><span class="contact-label">Address:</span> 4150 North Saguaro Way #210 Tucson, AZ 85716</li>
    </ul>
  </section>
</main>
</body>
</html>
```